Velmora Consulting Business

** Please add the content information from my old business card
1. I would like to see a two sided business card with both options with the 1st Option--Tallow Spire-new WHITE BACKGROUND LOGO
2 nd Option-Tallow Spire - new BLACK- Background Logo
3rd -Option a business card with my Photo on the card
Please add the new word to the card information:
EXECUTION
AS THE OWNER'S REP
WE AIM TO ACHIEVE YOUR
INFRASTRUCTURE VISION with
OUR SPECIALIZATION & EXECUTION in:

FUNDING Planning
BUSINESS Planning
INFRASTRUCTURE Planning
PROJECT Management
Since 2012
_____________________________________________________________________
I want to get spot uv raised printing. I was liking a a nice rich white linen paper stock with black writing & NOT A COLORED CARD other than a variety of white or black cards concept

```html
<!DOCTYPE html>
<html lang="en">
<head>
<meta charset="utf-8">
<title>Velmora Consulting – Business Card</title>
<link rel="stylesheet" href="https://fonts.googleapis.com/css2?family=Source+Sans+3:wght@400;600;700&display=swap">
<style>
  :root {
    --page-bg: #a3a3a3;
    --card-white: #f3f3f2;
    --card-black: #1c1c1c;
    --ink: #1a1a1a;
    --accent-red: #e31b3a;
    --paper-text: #ffffff;
    --mark-dark: #2e2e2e;
    --photo-top: #c9b9ad;
    --photo-bottom: #1e1e1e;
  }
  * { box-sizing: border-box; margin: 0; padding: 0; }
  html, body { width: 1093px; height: 1200px; overflow: hidden; }
  body {
    background: var(--page-bg);
    font-family: "Source Sans 3", "Helvetica Neue", Arial, sans-serif;
    position: relative;
  }
  .card {
    position: absolute;
    left: 265px;
    width: 580px;
    height: 357px;
    border-radius: 22px;
    overflow: hidden;
  }
  .card--front { top: 226px; background: var(--card-white); color: var(--ink); }
  .card--back { top: 621px; background: var(--card-black); color: var(--paper-text); }

  .portrait {
    position: absolute;
    left: 0; top: 0;
    width: 272px; height: 357px;
    background: linear-gradient(180deg, var(--card-white) 0%, var(--photo-top) 35%, var(--photo-bottom) 72%);
  }
  .brand-name {
    position: absolute;
    left: 288px; top: 58px;
    width: 200px;
    font-size: 36px;
    line-height: 1.05;
    font-weight: 700;
    color: var(--ink);
  }
  .person { position: absolute; left: 288px; top: 191px; }
  .person__name { font-size: 21px; font-weight: 700; line-height: 1.1; }
  .person__title { font-size: 14.5px; color: var(--accent-red); margin-top: 3px; letter-spacing: .1px; }
  .contact { position: absolute; left: 288px; top: 244px; list-style: none; }
  .contact__item {
    display: flex; align-items: center; gap: 9px;
    font-size: 16px; height: 21px;
  }
  .contact__icon { width: 15px; height: 15px; flex: none; }
  .locations { position: absolute; left: 288px; top: 317px; font-size: 16px; }
  .locations__sep { color: var(--accent-red); padding: 0 3px; }

  .back-mark {
    position: absolute;
    left: 342px; top: 96px;
    width: 200px;
    font-size: 38px;
    line-height: 1.05;
    font-weight: 700;
    color: var(--mark-dark);
  }
  .mission {
    position: absolute; left: 30px; top: 133px;
    font-size: 14px; line-height: 18.5px; text-transform: none;
  }
  .services {
    position: absolute; left: 30px; top: 263px;
    display: grid; grid-template-columns: 208px auto; row-gap: 1px;
    list-style: none; font-size: 14.5px;
  }
  .services__item { display: flex; align-items: center; gap: 7px; height: 18.5px; }
  .services__item::before {
    content: ""; width: 9px; height: 9px; background: var(--accent-red); flex: none;
  }
  .back-rule {
    position: absolute; left: 30px; top: 306px;
    width: 510px; height: 1px; background: var(--paper-text);
  }
  .since {
    position: absolute; right: 37px; top: 312px;
    font-size: 14.5px;
  }
</style>
</head>
<body>
  <section class="card card--front" aria-label="Business card front">
    <div class="portrait" role="img" aria-label="Portrait photo of the CEO, arms crossed, wearing a black top"></div>
    <div class="brand-name">Velmora Consulting</div>
    <div class="person">
      <div class="person__name">Marlene Whitcombe-Ardell</div>
      <div class="person__title">CEO / LEAD PROJECT MANAGER</div>
    </div>
    <ul class="contact">
      <li class="contact__item">
        <svg class="contact__icon" viewBox="0 0 16 16" aria-hidden="true"><path d="M4 1.5l2.2 3-1.3 1.6c.8 1.8 2.2 3.2 4 4l1.6-1.3 3 2.2-1 2.5C7.8 13.7 2.3 8.2 1.5 3z" fill="none" stroke="#1a1a1a" stroke-width="1.6" stroke-linejoin="round"/></svg>
        867.555.0148
      </li>
      <li class="contact__item">
        <svg class="contact__icon" viewBox="0 0 16 16" aria-hidden="true"><rect x="1" y="3.5" width="14" height="9.5" fill="#1a1a1a"/><path d="M1 3.5l7 5.5 7-5.5" fill="none" stroke="#f3f3f2" stroke-width="1.2"/></svg>
        marlene@velmora.ca
      </li>
      <li class="contact__item">
        <svg class="contact__icon" viewBox="0 0 16 16" aria-hidden="true"><g fill="none" stroke="#1a1a1a" stroke-width="1.3"><circle cx="8" cy="8" r="6.6"/><ellipse cx="8" cy="8" rx="3" ry="6.6"/><path d="M1.4 8h13.2M2.5 4.6h11M2.5 11.4h11"/></g></svg>
        www.velmora.ca
      </li>
    </ul>
    <div class="locations">Northgate NT<span class="locations__sep">•</span>Harrowmere NB</div>
  </section>

  <section class="card card--back" aria-label="Business card back">
    <div class="back-mark">Velmora Consulting</div>
    <p class="mission">
      EXECUTION<br>
      AS THE OWNER'S REP<br>
      WE AIM TO ACHIEVE YOUR<br>
      INFRASTRUCTURE VISION with<br>
      OUR SPECIALIZATION &amp; EXECUTION in:
    </p>
    <ul class="services">
      <li class="services__item">FUNDING Planning</li>
      <li class="services__item">BUSINESS Planning</li>
      <li class="services__item">INFRASTRUCTURE Planning</li>
      <li class="services__item">PROJECT Management</li>
    </ul>
    <div class="back-rule"></div>
    <div class="since">Since 2012</div>
  </section>
</body>
</html>
```